Coastal Learner Bureau business cards

Australian company about to start offering its services. We recruit international students to come to study English, vocational education and postgraduate courses in Australia. We help them find the institution and select the right city they want to come to Australia. We are a young, online oriented and supportive agency. Our clients are between 18 and 35 years old, mainly University students, young professionals or people with work experience. We provide much more information that any other agency offer. We administrate a Facebook group with more than 11.000 members that daily ask questions about general information when coming to Australia, while they are here and even after they leave the country

Target Market(s)

International students from South America, Central America and Europe

Industry/Entity Type

Student

Contact Information for Business Card

Tomas Bilbrea
Managing Director
tomas@kelvarin.com.au
www.kelvoria.com.au
+61 491058264
Melbourne, Australia

Font styles to use
Serif
Sans Serif

Colors

Designer to choose colors to be used in the design.

Requirements
Must have
• Horizontal design
• Standard business card size and shape. If font uses green or yellow colours, they will have to match the ones from the logo
Nice to have
• UPDATE: Use the contents of the green image to design one of the card sides. Use our logo in the background of that side as watermark.
• Passport image, or immigration stamps. A picture of the Yarra River (from Melbourne) would be cool as well.
Should not have
• Non-standard business card size and shape
• Not black as the background colour of any sides as we are not a VIP agency or a hight class service. We are orientes to young people and they like colours, pictures, something attractive.
• Vertical design
• NO YELLOW or BLACK AS THE BACKGROUND COLOUR OF ANY SIDE OF THE BIZ CARD

```html
<!DOCTYPE html>
<html lang="en">
<head>
<meta charset="utf-8">
<title>Coastal Learner Bureau business cards</title>
<link rel="stylesheet" href="https://fonts.googleapis.com/css2?family=Lato:ital,wght@0,400;0,700;1,400&family=Open+Sans:wght@400&display=swap">
<style>
  :root {
    --backdrop: #161616;
    --brand-green: #14603f;
    --brand-yellow: #e3b824;
    --yellow-fold: #a9851a;
    --paper: #faf8f3;
    --white: #ffffff;
  }
  * { box-sizing: border-box; margin: 0; padding: 0; }
  html, body {
    width: 1200px;
    height: 1000px;
    overflow: hidden;
    background: var(--backdrop);
  }
  .canvas {
    position: relative;
    width: 1200px;
    height: 1000px;
  }
  .card {
    position: absolute;
    top: 346px;
    width: 540px;
    height: 308px;
    overflow: hidden;
    box-shadow: 0 6px 18px rgba(0,0,0,0.55);
  }
  .card-front {
    left: 40px;
    background: var(--brand-green);
    display: flex;
    align-items: center;
    justify-content: center;
  }
  .wordmark {
    font-family: "Lato", sans-serif;
    font-weight: 700;
    font-size: 56px;
    letter-spacing: 0.5px;
    display: flex;
    align-items: center;
    gap: 14px;
  }
  .wordmark-dot {
    width: 18px;
    height: 18px;
    border-radius: 50%;
  }
  .card-front .wordmark { color: var(--white); }
  .card-front .wordmark-dot { background: var(--white); }

  .card-back {
    left: 620px;
    background: var(--paper);
  }
  .back-panel {
    position: absolute;
    left: 0; top: 0;
    width: 236px;
    height: 100%;
    background: var(--brand-green);
  }
  .name-ribbon {
    position: absolute;
    left: 0;
    top: 48px;
    width: 268px;
    height: 40px;
    background: var(--brand-yellow);
    color: var(--white);
    font-family: "Lato", sans-serif;
    font-weight: 700;
    font-size: 20px;
    line-height: 40px;
    padding-left: 42px;
  }
  .ribbon-fold {
    position: absolute;
    left: 250px;
    top: 88px;
    width: 0; height: 0;
    border-top: 14px solid var(--yellow-fold);
    border-right: 18px solid transparent;
  }
  .job-title {
    position: absolute;
    left: 42px;
    top: 110px;
    color: var(--white);
    font-family: "Lato", sans-serif;
    font-style: italic;
    font-size: 15px;
  }
  .contact-list {
    position: absolute;
    left: 22px;
    top: 150px;
    list-style: none;
    color: var(--white);
    font-family: "Open Sans", sans-serif;
    font-size: 14px;
  }
  .contact-list li {
    display: flex;
    align-items: center;
    gap: 10px;
    height: 22px;
  }
  .contact-icon {
    width: 13px;
    height: 13px;
    flex: none;
  }
  .brand-block {
    position: absolute;
    left: 236px;
    right: 0;
    top: 110px;
    display: flex;
    justify-content: center;
  }
  .card-back .wordmark {
    color: var(--brand-green);
    font-size: 48px;
  }
  .card-back .wordmark-dot { background: var(--brand-green); }
  .location {
    position: absolute;
    left: 268px;
    bottom: 30px;
    color: var(--brand-green);
    font-family: "Lato", sans-serif;
    font-weight: 700;
    font-size: 16px;
  }
</style>
</head>
<body>
<main class="canvas">
  <section class="card card-front" aria-label="Business card front">
    <div class="wordmark"><span class="wordmark-dot"></span>Kelvoria</div>
  </section>

  <section class="card card-back" aria-label="Business card back">
    <div class="back-panel"></div>
    <div class="name-ribbon">Tomas Bilbrea</div>
    <div class="ribbon-fold"></div>
    <p class="job-title">Managing director</p>
    <ul class="contact-list">
      <li>
        <svg class="contact-icon" viewBox="0 0 16 16" aria-hidden="true"><path fill="#fff" d="M4 1 L6.5 4.5 L5 6.5 C6 8.5 7.5 10 9.5 11 L11.5 9.5 L15 12 L13 15 C7 14.5 1.5 9 1 3 Z"/></svg>
        <span>+61 49 10 58 264</span>
      </li>
      <li>
        <svg class="contact-icon" viewBox="0 0 16 16" aria-hidden="true"><rect x="1" y="3" width="14" height="10" fill="#fff"/><path d="M1 3 L8 9 L15 3" fill="none" stroke="#14603f" stroke-width="1.4"/></svg>
        <span>tomas@kelvarin.com.au</span>
      </li>
      <li>
        <svg class="contact-icon" viewBox="0 0 16 16" aria-hidden="true"><g fill="none" stroke="#fff" stroke-width="1.4"><circle cx="8" cy="8" r="6.5"/><ellipse cx="8" cy="8" rx="2.8" ry="6.5"/><path d="M1.5 8 H14.5"/></g></svg>
        <span>www.kelvoria.com.au</span>
      </li>
    </ul>
    <div class="brand-block">
      <div class="wordmark"><span class="wordmark-dot"></span>Kelvoria</div>
    </div>
    <p class="location">Melbourne, Australia</p>
  </section>
</main>
</body>
</html>
```